Luxury Business Card Design for High-End Window Treatments

Gilded Slatworks
Custom Plantation Shutters & Architectural Shading Systems

⸻

BACK

Daniel Trevick
Owner

Custom Interior & Exterior Window Treatments

919-555-0148
gildedslatworks.com

I have included a picture that I’m hoping we can use on the back, but I’m also wondering if you can get rid of the ladder? Should we get rid of shutters , shades and blinds underneath Gilded Slatworks?

Target Market(s)

High-end residential homeowners, custom home builders, architects, interior designers, and luxury renovation clients seeking premium plantation shutters and motorized architectural shading systems.

Industry/Entity Type

Custom Window treatments

Contact Information for Business Card

Front Gilded Slatworks Custom Plantation Shutters Motorized Architectural Shading Systems BACK Daniel Trevick Owner 919-555-0148 GildedSlatworks.com Custom Interior & Exterior Window Treatments By Appointment

Requirements
Nice to have
• Not 100% sure on nice to halves or the color but you can definitely check out my website to get a better understanding of what I’m trying to do

```html
<!DOCTYPE html>
<html lang="en">
<head>
<meta charset="utf-8">
<title>Gilded Slatworks – Business Card</title>
<link href="https://fonts.googleapis.com/css2?family=Cormorant+Garamond:wght@500;600&family=Zilla+Slab:wght@700&family=Poppins:wght@400&display=swap" rel="stylesheet">
<style>
  :root {
    --backdrop: #bdbdbd;
    --card-black: #050505;
    --gold: #c0a850;
    --gold-bright: #d4b84f;
    --cream: #f6f0dc;
    --white: #ffffff;
    --sky: #6f9fd8;
    --screen: #2c3140;
  }
  * { margin: 0; padding: 0; box-sizing: border-box; }
  html, body { width: 1200px; height: 1015px; overflow: hidden; }
  body {
    background: var(--backdrop);
    position: relative;
    font-family: "Poppins", sans-serif;
  }
  .card {
    position: absolute;
    left: 250px;
    width: 700px;
    height: 400px;
    overflow: hidden;
    box-shadow: 0 10px 24px rgba(0,0,0,0.35);
  }
  .card--front { top: 80px; background: var(--card-black); }
  .card--back  { top: 535px; background: var(--card-black); }

  /* Front */
  .front-frame {
    position: absolute;
    inset: 28px 30px;
    border: 1px solid var(--gold);
  }
  .front-band {
    position: absolute;
    left: 52px; right: 48px; top: 225px; bottom: 22px;
    background: var(--gold);
    border: 1px solid var(--gold-bright);
    display: flex;
    align-items: flex-start;
    justify-content: center;
    padding-top: 22px;
  }
  .brand-name {
    position: absolute;
    left: 0; right: 0; top: 95px;
    text-align: center;
    font-family: "Cormorant Garamond", serif;
    font-weight: 600;
    font-size: 64px;
    line-height: 1;
    color: var(--gold-bright);
    letter-spacing: 1px;
  }
  .front-tagline {
    font-family: "Cormorant Garamond", serif;
    font-weight: 500;
    font-size: 21px;
    line-height: 1.2;
    text-align: center;
    color: var(--cream);
    letter-spacing: 0.5px;
  }

  /* Back */
  .back-photo {
    position: absolute;
    inset: 0;
    background:
      linear-gradient(180deg, rgba(0,0,0,0) 20%, rgba(0,0,0,0.55) 55%, rgba(0,0,0,0.92) 100%),
      linear-gradient(160deg, var(--sky) 0%, #c9c2ad 22%, var(--screen) 42%, #262a30 70%, #1b1d1a 100%);
  }
  .back-content {
    position: absolute;
    left: 40px; right: 40px; bottom: 28px;
  }
  .contact-row {
    display: flex;
    align-items: center;
    justify-content: center;
    gap: 22px;
    margin-bottom: 22px;
  }
  .person { text-align: right; }
  .person-name {
    font-family: "Zilla Slab", serif;
    font-weight: 700;
    font-size: 34px;
    line-height: 1;
    color: var(--gold-bright);
  }
  .person-role {
    font-size: 16px;
    color: var(--white);
    margin-top: 4px;
  }
  .divider {
    width: 1px;
    height: 56px;
    background: var(--gold);
  }
  .contact-list { list-style: none; }
  .contact-list li {
    display: flex;
    align-items: center;
    gap: 10px;
    font-size: 19px;
    color: var(--white);
    line-height: 1.45;
  }
  .contact-list svg { width: 18px; height: 18px; flex: none; }
  .back-tagline {
    font-family: "Cormorant Garamond", serif;
    font-weight: 600;
    font-size: 24px;
    text-align: center;
    color: var(--gold-bright);
    letter-spacing: 0.5px;
  }
</style>
</head>
<body>

<section class="card card--front">
  <div class="front-frame"></div>
  <h1 class="brand-name">Gilded Slatworks</h1>
  <div class="front-band">
    <p class="front-tagline">Gilded Slatworks Custom<br>Plantation Shutters Motorized<br>Architectural Shading Systems</p>
  </div>
</section>

<section class="card card--back">
  <div class="back-photo" role="img" aria-label="Photo of a covered porch fitted with dark motorized exterior shades between white columns, trees and blue sky above"></div>
  <div class="back-content">
    <div class="contact-row">
      <div class="person">
        <p class="person-name">Daniel Trevick</p>
        <p class="person-role">Owner</p>
      </div>
      <div class="divider"></div>
      <ul class="contact-list">
        <li>
          <svg viewBox="0 0 24 24" aria-hidden="true"><path fill="#d4b84f" d="M6.6 10.8a15.1 15.1 0 0 0 6.6 6.6l2.2-2.2a1 1 0 0 1 1-.25 11.4 11.4 0 0 0 3.6.57 1 1 0 0 1 1 1V20a1 1 0 0 1-1 1A17 17 0 0 1 3 4a1 1 0 0 1 1-1h3.5a1 1 0 0 1 1 1c0 1.25.2 2.45.57 3.6a1 1 0 0 1-.25 1z"/></svg>
          919-555-0148
        </li>
        <li>
          <svg viewBox="0 0 24 24" aria-hidden="true"><path fill="#d4b84f" d="M2 5h20v14H2z"/><path fill="none" stroke="#050505" stroke-width="1.8" d="M2 5l10 8 10-8"/></svg>
          GildedSlatworks.com
        </li>
      </ul>
    </div>
    <p class="back-tagline">Custom Interior &amp; Exterior Window Treatments By Appointment</p>
  </div>
</section>

</body>
</html>
```